New Business Card for Web Design/Internet Marketing Company

Looking for a great looking new business card. We are a 10 year old web design, internet marketing and website management company that works mostly with small businesses.

Our new card needs to better match the colors and style of our website, be bold, extremely usable and slightly edgy.

Target Market(s)

Small/Medium businesses that have websites

Industry/Entity Type

Internet

Requirements
Must have
• Front and back design, full color, rounded corners please

Must use the colors/style of our website (JPG provided)

INFO FOR CARDS (as readable as possible please)
Mark Lenner
President/CEO
mark@trelvanmedia.example
Phone: 520-381-7459
Toll Free: 866-381-7459
Address: 4315 W. Calloway Ave. Ste. 140, Tucson, AZ 85792

THINGS I WANT TO PROMOTE (if there is room):
1. Our Website - www.trelvanmedia.example

2. Social Media
Twitter: @trelvanmedia
Facebook: www.facebook.com/trelvanmedia

3. Our Services
Web Design
Internet Marketing
Website Management

```html
<!DOCTYPE html>
<html lang="en">
<head>
<meta charset="utf-8">
<title>Trelvan Media – Business Card</title>
<link href="https://fonts.googleapis.com/css2?family=Source+Sans+3:wght@400;600;700&display=swap" rel="stylesheet">
<style>
  :root {
    --orange: #f28634;
    --blue: #1e8fc6;
    --white: #ffffff;
    --backdrop: #e9e6e2;
    --card-shadow: rgba(0,0,0,0.25);
  }
  * { margin: 0; padding: 0; box-sizing: border-box; }
  html, body {
    width: 1200px; height: 1117px; overflow: hidden;
    background: var(--backdrop);
    font-family: "Source Sans 3", "Myriad Pro", sans-serif;
  }
  .canvas { position: relative; width: 1200px; height: 1117px; }

  .card { position: absolute; box-shadow: 0 3px 10px var(--card-shadow); overflow: hidden; }

  /* Front */
  .card-front { left: 80px; top: 81px; width: 802px; height: 457px; background: var(--white); }
  .front-brand {
    position: absolute; left: 0; top: 0; width: 418px; height: 457px;
    display: flex; align-items: center; justify-content: center; gap: 14px;
  }
  .brand-dot { width: 26px; height: 26px; border-radius: 50%; background: var(--blue); }
  .brand-name { font-weight: 700; font-size: 44px; color: var(--orange); letter-spacing: -0.5px; }
  .front-divider { position: absolute; left: 418px; top: 0; width: 4px; height: 457px; background: var(--blue); }
  .front-info {
    position: absolute; left: 426px; top: 0; right: 0; bottom: 0;
    background: var(--orange); color: var(--white); padding: 88px 0 0 28px;
  }
  .person { font-size: 27px; font-weight: 700; line-height: 1; }
  .person .title { font-size: 21px; font-weight: 400; }
  .contact-list { list-style: none; margin-top: 34px; }
  .contact-list li { display: flex; align-items: center; gap: 10px; font-size: 19px; height: 29px; }
  .contact-list svg { width: 15px; height: 15px; flex: none; }
  .address { margin-top: 26px; font-size: 19px; line-height: 26px; }

  /* Back */
  .card-back {
    left: 318px; top: 596px; width: 803px; height: 459px; background: var(--orange);
    color: var(--white); text-align: center;
  }
  .back-brand { position: absolute; top: 118px; left: 0; right: 0;
    display: flex; justify-content: center; align-items: center; gap: 18px; }
  .back-brand .brand-name { color: var(--white); font-size: 72px; }
  .back-brand .brand-dot { background: var(--white); width: 38px; height: 38px; }
  .services { position: absolute; top: 296px; left: 0; right: 0; font-size: 26px; font-weight: 700; line-height: 36px; }
  .services span { margin: 0 10px; }
  .services span::before { content: "● "; font-size: 18px; vertical-align: 3px; }
  .social { position: absolute; top: 380px; left: 0; right: 0; font-size: 26px;
    display: flex; justify-content: center; gap: 22px; }
  .social-item { display: flex; align-items: center; gap: 8px; }
  .social-mark { width: 18px; height: 18px; background: #4a86c5; border: 1px solid var(--white); }
</style>
</head>
<body>
<main class="canvas">
  <section class="card card-front">
    <div class="front-brand">
      <span class="brand-dot"></span>
      <span class="brand-name">Trelvan Media</span>
    </div>
    <div class="front-divider"></div>
    <div class="front-info">
      <p class="person">Mark Lenner , <span class="title">President/CEO</span></p>
      <ul class="contact-list">
        <li><svg viewBox="0 0 16 16"><circle cx="8" cy="8" r="7" fill="none" stroke="#fff" stroke-width="1.4"/><path d="M5 4.5l1.6 0 .8 2-1 .8a5 5 0 0 0 2.3 2.3l.8-1 2 .8v1.6c-4 .5-7-2.5-6.5-6.5z" fill="#fff"/></svg>866-381-7459</li>
        <li><svg viewBox="0 0 16 16"><circle cx="8" cy="8" r="7" fill="none" stroke="#fff" stroke-width="1.4"/><path d="M5 4.5l1.6 0 .8 2-1 .8a5 5 0 0 0 2.3 2.3l.8-1 2 .8v1.6c-4 .5-7-2.5-6.5-6.5z" fill="#fff"/></svg>520-381-7459</li>
        <li><svg viewBox="0 0 16 16"><circle cx="8" cy="8" r="8" fill="#fff"/><rect x="3.5" y="5" width="9" height="6" fill="none" stroke="#f28634" stroke-width="1.2"/><path d="M3.5 5l4.5 3.5L12.5 5" fill="none" stroke="#f28634" stroke-width="1.2"/></svg>mark@trelvanmedia.example</li>
        <li><svg viewBox="0 0 16 16"><circle cx="8" cy="8" r="8" fill="#fff"/><path d="M0.5 8h15M8 .5c-3 3-3 12 0 15M8 .5c3 3 3 12 0 15" fill="none" stroke="#f28634" stroke-width="1.1"/></svg>www.trelvanmedia.example</li>
      </ul>
      <p class="address">4315 W. Calloway Ave. Ste. 140<br>Tucson, AZ 85792</p>
    </div>
  </section>

  <section class="card card-back">
    <div class="back-brand">
      <span class="brand-dot"></span>
      <span class="brand-name">Trelvan Media</span>
    </div>
    <p class="services"><span>Web Design</span><span>Internet Marketing</span><br><span>Website Management</span></p>
    <div class="social">
      <span class="social-item"><span class="social-mark"></span>@trelvanmedia</span>
      <span class="social-item"><span class="social-mark"></span>trelvanmedia</span>
    </div>
  </section>
</main>
</body>
</html>
```